4747 5858

Web(re)design of an existing directory search site www.le5858.be (in Dutch www.de4747.be and in English www.3838.be).

This site is a directory site, i.e. a "white pages" site whereby people can search the phone & details of another person based on a combination of name + city (for instance smith in Brussels); one can also search a company also based on a combination of name + city (for instance Vornak in Brussels); last but not least one can also search the name of the subscriber behind a specific telephone number (also called reverse search).

This site is quite outdated and needs a redesign, see instructions.

We need the output in XD format.

```html
<!DOCTYPE html>
<html lang="en">
<head>
<meta charset="utf-8">
<title>4747 5858 — Directory</title>
<link href="https://fonts.googleapis.com/css2?family=Poppins:wght@400;500;600;700&display=swap" rel="stylesheet">
<style>
:root{
  --red:#c8161d;
  --ink:#1b1b1b;
  --muted:#6b6b6b;
  --soft:#f4f4f4;
  --line:#e3e3e3;
  --footer:#1a1a1a;
  --white:#fff;
}
*{box-sizing:border-box;margin:0;padding:0}
html,body{width:1200px;height:2585px;overflow:hidden}
body{font-family:'Poppins',sans-serif;color:var(--ink);background:var(--white);position:relative}
.abs{position:absolute}

/* header */
.site-header{position:absolute;top:0;left:0;width:1200px;height:95px;border-bottom:4px solid var(--red);background:var(--white)}
.brand{position:absolute;left:111px;top:30px;display:flex;align-items:center;gap:8px;color:var(--red);font-weight:700;font-size:20px}
.brand .dot{width:14px;height:14px;border-radius:50%;background:var(--red)}
.main-nav{position:absolute;left:327px;top:38px;display:flex;gap:28px;font-size:14px;font-weight:600;color:#555}
.main-nav .active{color:var(--red)}
.account-btn{position:absolute;left:916px;top:22px;width:52px;height:52px;border-radius:50%;background:var(--white);box-shadow:0 2px 10px rgba(0,0,0,.12);display:flex;align-items:center;justify-content:center}
.account-label{position:absolute;left:988px;top:38px;font-size:14px;font-weight:600}

/* hero */
.hero{position:absolute;top:99px;left:0;width:1200px;height:557px;background:linear-gradient(100deg,#c9b79f 0%,#e8dfd2 30%,#eeeae5 55%,#d9d9da 100%)}
.hero-title{position:absolute;top:308px;left:0;width:1200px;text-align:center;font-size:29px;font-weight:500;color:#111}
.search-bar{position:absolute;top:385px;left:193px;width:814px;height:53px;background:var(--white);border-radius:27px;display:flex;overflow:hidden;box-shadow:0 3px 12px rgba(0,0,0,.1)}
.search-field{flex:0 0 227px;display:flex;align-items:center;gap:12px;padding-left:24px;font-size:15px;color:#777;border-right:1px solid var(--line)}
.search-field:nth-child(3){border-right:none;flex-basis:226px}
.search-submit{flex:1;background:var(--red);color:var(--white);font-weight:700;font-size:14px;display:flex;align-items:center;justify-content:center}
.hero-badge{position:absolute;top:600px;left:544px;width:112px;height:112px;border-radius:50%;border:1px solid var(--white);display:flex;align-items:center;justify-content:center}
.hero-badge span{width:70px;height:70px;border-radius:50%;background:var(--white);box-shadow:0 3px 10px rgba(0,0,0,.15);display:flex;align-items:center;justify-content:center;color:var(--red);font-weight:700;font-size:13px}

.section-title{position:absolute;left:0;width:1200px;text-align:center;font-size:36px;font-weight:500}
.rule{position:absolute;height:3px;background:var(--red)}

/* categories */
.category-card{position:absolute;top:866px;width:222px;height:188px;background:var(--white);border-radius:6px;box-shadow:0 2px 12px rgba(0,0,0,.1);text-align:center}
.category-card svg{margin-top:40px}
.category-card h3{position:absolute;top:124px;width:100%;font-size:23px;font-weight:500;letter-spacing:.5px}
.category-card.is-active{border-bottom:4px solid var(--red)}
.carousel-arrow{position:absolute;top:950px}

/* international */
.intl{position:absolute;top:1148px;left:0;width:1200px;height:552px;background:var(--soft)}
.intl h2{position:absolute;left:109px;top:95px;font-size:28px;font-weight:500}
.intl-text{position:absolute;left:111px;top:172px;width:437px;font-size:14.5px;line-height:25px;color:var(--muted);text-align:justify}
.intl-text p+p{margin-top:14px}
.btn{position:absolute;left:111px;top:399px;width:141px;height:51px;border-radius:26px;background:var(--red);color:var(--white);font-weight:600;font-size:14px;display:flex;align-items:center;justify-content:center}
.intl-photo{position:absolute;left:600px;top:84px;width:489px;height:385px;background:linear-gradient(135deg,#c9b9a4,#8d7a66 45%,#4f6f8f 75%,#d8cfc4)}

/* press */
.press-card{position:absolute;top:1881px;width:309px;text-align:center}
.press-photo{height:215px;border-radius:10px}
.press-date{margin-top:24px;font-size:15.5px;color:var(--muted);display:flex;justify-content:center;align-items:center;gap:10px}
.press-card h3{margin-top:8px;font-size:18px;font-weight:500;line-height:22px;padding:0 18px}
.press-divider{position:absolute;top:1881px;width:1px;height:318px;background:var(--line)}

/* footer */
.site-footer{position:absolute;top:2283px;left:0;width:1200px;height:302px;background:var(--footer);color:var(--white)}
.footer-col{position:absolute;top:48px}
.footer-col h4{font-size:17px;font-weight:600;margin-bottom:26px}
.footer-col li{list-style:none;font-size:14.5px;display:flex;align-items:flex-start;gap:18px;height:28px}
.footer-col li svg{flex:0 0 auto;margin-top:4px}
.country-select{width:232px;height:50px;border-radius:25px;background:var(--white);color:var(--ink);font-size:15px;display:flex;align-items:center;justify-content:space-between;padding:0 18px}
.footer-rule{position:absolute;left:111px;top:246px;width:978px;height:1px;background:#3a3a3a}
.copyright{position:absolute;top:265px;left:0;width:1200px;text-align:center;font-size:14px}
</style>
</head>
<body>

<header class="site-header">
  <div class="brand"><span class="dot"></span>4747 5858</div>
  <nav class="main-nav">
    <span class="active">INDIVIDUALS</span><span>COMPANIES</span><span>INVERSED ANNUAL</span><span>INTERNATIONAL</span>
  </nav>
  <div class="account-btn">
    <svg width="18" height="18" viewBox="0 0 18 18"><circle cx="9" cy="9" r="8" fill="none" stroke="#c8161d" stroke-width="2"/><circle cx="9" cy="7" r="3" fill="#c8161d"/><path d="M4 14c1.5-3 8.5-3 10 0" fill="#c8161d"/></svg>
  </div>
  <div class="account-label">MY ACCOUNT</div>
</header>

<section class="hero" role="img" aria-label="Photo of a smiling young woman wearing a headset, working on a laptop in a bright room"></section>
<h1 class="hero-title">Easily find what you are looking for</h1>
<form class="search-bar">
  <div class="search-field"><svg width="16" height="16" viewBox="0 0 16 16"><circle cx="8" cy="8" r="7" fill="none" stroke="#222" stroke-width="1.6"/><circle cx="8" cy="6.5" r="2.5" fill="#222"/><path d="M3.5 12.5c1.5-3 7.5-3 9 0" fill="#222"/></svg>Surname</div>
  <div class="search-field"><svg width="16" height="16" viewBox="0 0 16 16"><circle cx="8" cy="8" r="7" fill="none" stroke="#222" stroke-width="1.6"/><circle cx="8" cy="6.5" r="2.5" fill="#222"/><path d="M3.5 12.5c1.5-3 7.5-3 9 0" fill="#222"/></svg>First name</div>
  <div class="search-field"><svg width="10" height="14" viewBox="0 0 10 14"><path d="M5 0a5 5 0 0 1 5 5c0 3.5-5 9-5 9S0 8.5 0 5a5 5 0 0 1 5-5z" fill="#222"/><circle cx="5" cy="5" r="1.8" fill="#fff"/></svg>Location</div>
  <div class="search-submit">FIND NOW</div>
</form>
<div class="hero-badge"><span>5858</span></div>

<h2 class="section-title" style="top:758px">Popular Categories</h2>
<div class="rule" style="left:543px;top:813px;width:112px"></div>

<svg class="carousel-arrow" style="left:53px" width="14" height="20" viewBox="0 0 14 20"><path d="M10 2 3 10l7 8" fill="none" stroke="#bbb" stroke-width="2"/></svg>
<svg class="carousel-arrow" style="left:1133px" width="14" height="20" viewBox="0 0 14 20"><path d="M4 2l7 8-7 8" fill="none" stroke="#111" stroke-width="2.4"/></svg>

<div class="category-card" style="left:111px">
  <svg width="60" height="60" viewBox="0 0 60 60" fill="none" stroke="#c8161d" stroke-width="2"><rect x="8" y="8" width="44" height="50"/><path d="M4 58h52M20 2h20v6"/><g><rect x="14" y="14" width="6" height="6"/><rect x="27" y="14" width="6" height="6"/><rect x="40" y="14" width="6" height="6"/><rect x="14" y="26" width="6" height="6"/><rect x="27" y="26" width="6" height="6"/><rect x="40" y="26" width="6" height="6"/><rect x="14" y="38" width="6" height="6"/><rect x="40" y="38" width="6" height="6"/></g><rect x="25" y="44" width="10" height="14"/></svg>
  <h3>OFFICE</h3>
</div>
<div class="category-card" style="left:362px">
  <svg width="60" height="60" viewBox="0 0 60 60" fill="none" stroke="#c8161d" stroke-width="2"><path d="M2 40 18 12l10 14 8-8 22 22"/><path d="M12 58V44M6 52l6-10 6 10zM20 58V46M15 54l5-9 5 9z"/><path d="M36 58l6-10 6 10M30 58h28"/></svg>
  <h3>TOURIST</h3>
</div>
<div class="category-card is-active" style="left:613px">
  <svg width="64" height="60" viewBox="0 0 64 60"><rect x="2" y="2" width="36" height="56" fill="#c8161d"/><rect x="38" y="28" width="24" height="30" fill="#c8161d"/><g fill="#fff"><rect x="7" y="16" width="7" height="7"/><rect x="17" y="16" width="7" height="7"/><rect x="27" y="16" width="7" height="7"/><rect x="7" y="28" width="7" height="7"/><rect x="17" y="28" width="7" height="7"/><rect x="27" y="28" width="7" height="7"/><rect x="7" y="40" width="7" height="7"/><rect x="27" y="40" width="7" height="7"/><rect x="16" y="44" width="9" height="14"/><rect x="43" y="34" width="6" height="6"/><rect x="52" y="34" width="6" height="6"/><rect x="43" y="45" width="6" height="6"/><rect x="52" y="45" width="6" height="6"/><rect x="6" y="5" width="28" height="6"/></g></svg>
  <h3>HOTEL</h3>
</div>
<div class="category-card" style="left:864px">
  <svg width="60" height="60" viewBox="0 0 60 60" fill="none" stroke="#c8161d" stroke-width="2"><path d="M30 4l14 6v12c0 10-7 16-14 19-7-3-14-9-14-19V10z"/><path d="M30 14v14M23 21h14" stroke-width="3"/><path d="M4 26v14l12 12v6M56 26v14L44 52v6M10 36l8 8M50 36l-8 8"/></svg>
  <h3>HEALTH</h3>
</div>

<section class="intl">
  <h2>International Enquiries</h2>
  <div class="rule" style="left:111px;top:138px;width:94px"></div>
  <div class="intl-text">
    <p>For international enquiries, we also suggest you call 58-58 , our experienced operators will be there to help you and will certainly find you the desired number.</p>
    <p>Whether looking for the number of a hotel in Benidorm, that of the tourist office in Saint-Tropez or that of a friend living in Italy, or even to find a supplier located in London or Amsterdam, the 58-58 also allows</p>
  </div>
  <div class="btn">LEARN MORE</div>
  <div class="intl-photo" role="img" aria-label="Photo of a smiling man with glasses using his smartphone at a laptop in a living room"></div>
</section>

<h2 class="section-title" style="top:1786px">Press Releases</h2>
<div class="rule" style="left:552px;top:1840px;width:94px"></div>

<article class="press-card" style="left:111px">
  <div class="press-photo" role="img" aria-label="Photo of a young woman working on a laptop at a café table" style="background:linear-gradient(135deg,#e6ddd0,#a88c6e 60%,#6c5a49)"></div>
  <div class="press-date"><svg width="14" height="14" viewBox="0 0 14 14"><rect x="1" y="2" width="12" height="11" fill="none" stroke="#c8161d" stroke-width="1.5"/><path d="M1 5h12M4 0v3M10 0v3" stroke="#c8161d" stroke-width="1.5"/></svg>05 Dec 2008</div>
  <h3>This year, Saint Nicolas will pass on December 13</h3>
</article>
<div class="press-divider" style="left:432px"></div>
<article class="press-card" style="left:445px">
  <div class="press-photo" role="img" aria-label="Photo of a couple looking at a tablet together" style="background:linear-gradient(135deg,#5d6472,#b89a80 50%,#ece7df)"></div>
  <div class="press-date"><svg width="14" height="14" viewBox="0 0 14 14"><rect x="1" y="2" width="12" height="11" fill="none" stroke="#c8161d" stroke-width="1.5"/><path d="M1 5h12M4 0v3M10 0v3" stroke="#c8161d" stroke-width="1.5"/></svg>25 Mar 2008</div>
  <h3>Northline Directory Services finalizes a capital increase</h3>
</article>
<div class="press-divider" style="left:766px"></div>
<article class="press-card" style="left:779px">
  <div class="press-photo" role="img" aria-label="Photo of an older woman with glasses checking her phone at a laptop" style="background:linear-gradient(135deg,#8ea28b,#6b6f74 50%,#c9c5bf)"></div>
  <div class="press-date"><svg width="14" height="14" viewBox="0 0 14 14"><rect x="1" y="2" width="12" height="11" fill="none" stroke="#c8161d" stroke-width="1.5"/><path d="M1 5h12M4 0v3M10 0v3" stroke="#c8161d" stroke-width="1.5"/></svg>16 Nov 2007</div>
  <h3>Le 58-58 concludes a partnership with Datavia</h3>
</article>

<footer class="site-footer">
  <div class="footer-col" style="left:111px">
    <h4>SELECT A COUNTRY</h4>
    <div class="country-select">Denmark<svg width="10" height="6" viewBox="0 0 10 6"><path d="M1 1l4 4 4-4" fill="none" stroke="#222" stroke-width="1.4"/></svg></div>
  </div>
  <div class="footer-col" style="left:402px">
    <h4>QUICK LINKS</h4>
    <ul>
      <li><svg width="14" height="14" viewBox="0 0 14 14"><circle cx="7" cy="7" r="7" fill="#c8161d"/><path d="M6 4l3 3-3 3" fill="none" stroke="#1a1a1a" stroke-width="1.6"/></svg>Individuals</li>
      <li><svg width="14" height="14" viewBox="0 0 14 14"><circle cx="7" cy="7" r="7" fill="#c8161d"/><path d="M6 4l3 3-3 3" fill="none" stroke="#1a1a1a" stroke-width="1.6"/></svg>Companies</li>
      <li><svg width="14" height="14" viewBox="0 0 14 14"><circle cx="7" cy="7" r="7" fill="#c8161d"/><path d="M6 4l3 3-3 3" fill="none" stroke="#1a1a1a" stroke-width="1.6"/></svg>Inversed Annual</li>
      <li><svg width="14" height="14" viewBox="0 0 14 14"><circle cx="7" cy="7" r="7" fill="#c8161d"/><path d="M6 4l3 3-3 3" fill="none" stroke="#1a1a1a" stroke-width="1.6"/></svg>International</li>
    </ul>
  </div>
  <div class="footer-col" style="left:625px">
    <h4>OTHER LINKS</h4>
    <ul>
      <li><svg width="14" height="14" viewBox="0 0 14 14"><circle cx="7" cy="7" r="7" fill="#c8161d"/><path d="M6 4l3 3-3 3" fill="none" stroke="#1a1a1a" stroke-width="1.6"/></svg>B2B Services</li>
      <li><svg width="14" height="14" viewBox="0 0 14 14"><circle cx="7" cy="7" r="7" fill="#c8161d"/><path d="M6 4l3 3-3 3" fill="none" stroke="#1a1a1a" stroke-width="1.6"/></svg>Help</li>
      <li><svg width="14" height="14" viewBox="0 0 14 14"><circle cx="7" cy="7" r="7" fill="#c8161d"/><path d="M6 4l3 3-3 3" fill="none" stroke="#1a1a1a" stroke-width="1.6"/></svg>Terms of Use</li>
      <li><svg width="14" height="14" viewBox="0 0 14 14"><circle cx="7" cy="7" r="7" fill="#c8161d"/><path d="M6 4l3 3-3 3" fill="none" stroke="#1a1a1a" stroke-width="1.6"/></svg>Respect for privacy</li>
    </ul>
  </div>
  <div class="footer-col" style="left:884px">
    <h4>CONTACT</h4>
    <ul>
      <li style="height:60px;line-height:26px"><svg width="14" height="14" viewBox="0 0 10 14"><path d="M5 0a5 5 0 0 1 5 5c0 3.5-5 9-5 9S0 8.5 0 5a5 5 0 0 1 5-5z" fill="#c8161d"/><circle cx="5" cy="5" r="1.8" fill="#1a1a1a"/></svg><span>Rue des Lilas 27<br>B-1040 Brussels</span></li>
      <li style="height:34px"><svg width="14" height="14" viewBox="0 0 14 14"><rect x="1" y="4" width="12" height="9" rx="1" fill="#c8161d"/><rect x="3" y="1" width="8" height="4" fill="none" stroke="#c8161d" stroke-width="1.5"/></svg>+32 (2) 555 01 23</li>
      <li><svg width="14" height="14" viewBox="0 0 14 11"><rect width="14" height="11" rx="1" fill="#c8161d"/><path d="M0 1l7 5 7-5" fill="none" stroke="#1a1a1a" stroke-width="1.3"/></svg>info@le5858.be</li>
    </ul>
  </div>
  <div class="footer-rule"></div>
  <div class="copyright">© 2022 <strong>le 5858</strong> &nbsp;|&nbsp; All Rights Reserved</div>
</footer>

</body>
</html>
```